Business card design for my company.
I would like the card's background colour to be black. You can also see our web site to get an idea of our brand. https://www.tmwhomecrafting.com.au/
- Name
- Email

```html
<!DOCTYPE html>
<html lang="en">
<head>
<meta charset="utf-8">
<title>TMW Home Crafting – Business Card</title>
<link href="https://fonts.googleapis.com/css2?family=Montserrat:wght@400;500;700;800&display=swap" rel="stylesheet">
<style>
  :root {
    --stage: #3a3a3a;
    --card: #222222;
    --card-back: #1f1f1f;
    --green: #1f9a45;
    --white: #f2f2f2;
    --muted: #2c2c2c;
    --band-light: #4a4a4a;
    --band-dark: #161616;
  }
  * { box-sizing: border-box; margin: 0; padding: 0; }
  html, body { width: 1200px; height: 875px; overflow: hidden; }
  body {
    background: var(--stage);
    font-family: "Montserrat", sans-serif;
    position: relative;
  }
  .card {
    position: absolute;
    left: 320px;
    width: 560px;
    height: 320px;
    border-radius: 22px;
    overflow: hidden;
    box-shadow: 0 14px 30px rgba(0,0,0,.45);
  }
  .card--back { top: 90px; background: var(--card-back); }
  .card--front { top: 465px; background: var(--card); }

  .back-mark {
    position: absolute;
    inset: 0;
    padding: 40px 60px;
    display: flex;
    align-items: center;
    justify-content: center;
    text-align: center;
    font-weight: 800;
    font-size: 38px;
    line-height: 1.15;
    letter-spacing: 2px;
    text-transform: uppercase;
    color: var(--muted);
  }

  .accent-tab {
    position: absolute;
    top: 34px; right: 0;
    width: 18px; height: 36px;
    background: var(--green);
  }
  .person {
    position: absolute;
    top: 34px; right: 30px;
    text-align: right;
  }
  .person__name {
    font-weight: 800;
    font-size: 24px;
    letter-spacing: .5px;
    color: var(--green);
    text-transform: uppercase;
    line-height: 1.1;
  }
  .person__role {
    font-weight: 400;
    font-size: 14px;
    color: var(--white);
  }

  .brand {
    position: absolute;
    left: 48px; top: 118px;
    display: flex;
    align-items: center;
    gap: 12px;
  }
  .brand__square { width: 22px; height: 22px; background: var(--green); flex: none; }
  .brand__name {
    font-weight: 800;
    font-size: 26px;
    color: var(--white);
    text-transform: uppercase;
    letter-spacing: 1px;
    white-space: nowrap;
  }

  .contact {
    position: absolute;
    left: 48px; bottom: 36px;
    list-style: none;
    display: flex;
    flex-direction: column;
    gap: 7px;
  }
  .contact__item {
    display: flex;
    align-items: center;
    gap: 10px;
    font-size: 14px;
    color: var(--white);
    white-space: nowrap;
  }
  .contact__item svg { width: 13px; height: 13px; fill: var(--green); flex: none; }
  .contact__highlight { color: var(--green); }

  .corner-band {
    position: absolute;
    right: 0; bottom: 0;
    width: 230px; height: 320px;
  }
</style>
</head>
<body>

  <section class="card card--back" aria-label="Card back">
    <div class="back-mark">TMW Home Crafting</div>
  </section>

  <section class="card card--front" aria-label="Card front">
    <svg class="corner-band" viewBox="0 0 230 320" aria-hidden="true">
      <defs>
        <linearGradient id="bandShade" x1="0" y1="1" x2="1" y2="0">
          <stop offset="0" stop-color="var(--band-dark)"/>
          <stop offset="1" stop-color="var(--band-light)"/>
        </linearGradient>
      </defs>
      <polygon points="30,320 140,130 230,130 230,150 152,150 62,320" fill="url(#bandShade)"/>
    </svg>

    <div class="accent-tab"></div>
    <div class="person">
      <p class="person__name">Dorian Hale</p>
      <p class="person__role">CEO/Founder</p>
    </div>

    <div class="brand">
      <span class="brand__square"></span>
      <span class="brand__name">TMW Home Crafting</span>
    </div>

    <ul class="contact">
      <li class="contact__item">
        <svg viewBox="0 0 24 24"><path d="M6.6 10.8a15.1 15.1 0 0 0 6.6 6.6l2.2-2.2a1 1 0 0 1 1-.25 11.4 11.4 0 0 0 3.6.57 1 1 0 0 1 1 1V20a1 1 0 0 1-1 1A17 17 0 0 1 3 4a1 1 0 0 1 1-1h3.5a1 1 0 0 1 1 1c0 1.25.2 2.45.57 3.57a1 1 0 0 1-.25 1z"/></svg>
        555-214-7730
      </li>
      <li class="contact__item">
        <svg viewBox="0 0 24 24"><path d="M2 5h20v14H2z M2 5l10 8 10-8"/></svg>
        info@tmwhomecrafting.com.au
      </li>
      <li class="contact__item">
        <svg viewBox="0 0 24 24"><circle cx="12" cy="12" r="10"/></svg>
        <span>www.<span class="contact__highlight">tmwhomecrafting</span>.com.au</span>
      </li>
    </ul>
  </section>

</body>
</html>
```